Firm-Asset: Tomorrow - EU-funded management consulting

A website to inform possible customers about my management consulting services for small and medium sized companies. I am using a funding for small and medium companies to do 10 days of workshops and coaching about leadership, further education and employee's health. The Funding is called "Betriebsgut Zukunft" which means something like: Humans are the value of the company. The official logo is attached as a

Target Market(s)

Small and medium sized companies that want to improve their employee's well being and efficiency.

Industry/Entity Type

Management Consulting

Contact Information for Business Card

Malte Quast, Birkenhainweg 14, 10219 Berlin

Logo Text

BetriebsGut Zukunft - Beratung

Font styles to use
Serif
Sans Serif

Requirements
Must have
• a friendly and professional design
Nice to have
• saying somthing about: employees, leadership, further education and employees health are important to us.
Should not have
• should not be too shimmering

```html
<!DOCTYPE html>
<html lang="en">
<head>
<meta charset="utf-8">
<title>Betriebsgut Zukunft – Beratung</title>
<link href="https://fonts.googleapis.com/css2?family=Raleway:wght@400;600;700;800&family=Open+Sans:wght@400;600;700&display=swap" rel="stylesheet">
<style>
:root{
  --blue:#1d4f7c;
  --blue-dark:#163d60;
  --orange:#e4892b;
  --text:#555;
  --heading:#333;
  --band:#efefef;
  --line:#dcdcdc;
  --footer:#121212;
  --white:#fff;
}
*{box-sizing:border-box;margin:0;padding:0}
html,body{width:789px;height:1200px;overflow:hidden;background:var(--white)}
body{font-family:"Open Sans",sans-serif;color:var(--text);font-size:8px;line-height:1.5}
.page{position:relative;width:789px;height:1200px}

/* header */
.topbar{height:70px;display:flex;align-items:center;padding:0 38px;justify-content:space-between}
.brand{display:flex;align-items:center;gap:8px}
.brand-mark{width:22px;height:22px;background:var(--blue)}
.brand-name{font-family:"Raleway",sans-serif;font-weight:700;font-size:15px;color:var(--blue);line-height:1.1}
.brand-name small{display:block;font-size:9px;font-weight:700}
.search{display:flex;width:235px;height:20px;border:1px solid var(--line);margin-left:-40px}
.search span{flex:1}
.search b{width:24px;background:var(--blue);display:flex;align-items:center;justify-content:center}
.contact{font-size:8px;line-height:1.9;text-align:left}
.contact strong{color:var(--orange);font-weight:700;margin-right:6px}
.nav{height:36px;display:flex;align-items:center;justify-content:space-between;padding:0 38px;border-top:1px solid var(--line)}
.nav ul{list-style:none;display:flex;gap:30px}
.nav a{font-family:"Raleway",sans-serif;font-weight:700;font-size:9px;color:var(--heading);text-decoration:none}
.nav a.active{color:var(--orange)}
.social{display:flex;gap:9px}
.social i{width:18px;height:18px;border-radius:50%;background:var(--blue)}

/* hero */
.hero{position:relative;height:315px;background:linear-gradient(90deg,#8e98a3 0%,#c9cfd6 45%,#e8ebee 75%,#d3d9df 100%)}
.hero-text{position:absolute;left:33px;top:64px;color:var(--white)}
.hero-text h1{font-family:"Raleway",sans-serif;font-weight:800;font-size:21px;letter-spacing:1.5px}
.hero-text p{font-family:"Raleway",sans-serif;font-size:20px;letter-spacing:2px;margin-top:8px}
.btn{display:inline-block;font-family:"Raleway",sans-serif;font-weight:700;font-size:7.5px;color:var(--white);background:var(--blue);padding:6px 14px;text-decoration:none;text-transform:uppercase}
.btn-ghost{background:transparent;border:1px solid var(--white);margin-top:40px}
.arrow{position:absolute;top:50%;width:20px;height:20px;margin-top:-10px;border-radius:50%;background:rgba(255,255,255,.85);display:flex;align-items:center;justify-content:center}
.arrow.prev{left:4px}.arrow.next{right:4px}

/* sections */
.section-title{font-family:"Raleway",sans-serif;font-weight:700;text-align:center;color:var(--orange);font-size:13px;letter-spacing:.5px}
.welcome{height:200px;padding-top:56px;text-align:center}
.welcome p{width:450px;margin:10px auto 18px;font-size:7.5px}
.services{height:322px;background:var(--band);padding-top:14px}
.services .kicker{text-align:center;font-family:"Raleway",sans-serif;font-weight:700;font-size:8px;color:var(--heading)}
.cards{display:flex;justify-content:center;gap:13px;margin-top:18px}
.card{width:213px}
.card .photo{height:112px}
.card h3{font-family:"Raleway",sans-serif;font-weight:700;font-size:8.5px;color:var(--heading);margin:12px 0 4px;text-transform:uppercase}
.card p{font-size:7.5px;margin-bottom:10px}
.ph-lead{background:linear-gradient(135deg,#f2f2f2,#9a9a9a)}
.ph-health{background:linear-gradient(135deg,#6c7d8c,#b9a793)}
.ph-edu{background:linear-gradient(135deg,#e2e2e2,#7e7e7e)}

.testimonials{height:205px;padding-top:24px}
.quotes{display:flex;justify-content:center;gap:26px;margin-top:18px}
.quote{width:326px;border:1px solid var(--line);padding:10px 12px 8px;position:relative;height:82px}
.quote p{font-size:7.5px}
.person{position:absolute;left:18px;bottom:-22px;display:flex;align-items:center;gap:8px}
.avatar{width:26px;height:26px;border-radius:50%;background:#a7a7a7;border:2px solid var(--white)}
.person span{font-family:"Raleway",sans-serif;font-weight:700;font-size:7px;color:var(--heading);margin-top:18px}
.pager{text-align:center;margin-top:34px;font-size:10px;color:var(--blue);font-weight:700}

.footer{position:absolute;left:0;bottom:0;width:100%;height:48px;background:var(--footer);color:#bbb;display:flex;align-items:center;justify-content:space-between;padding:0 64px;font-size:6.5px}
</style>
</head>
<body>
<div class="page">
  <header>
    <div class="topbar">
      <div class="brand">
        <span class="brand-mark"></span>
        <span class="brand-name">Betriebsgut Zukunft<small>Beratung</small></span>
      </div>
      <div class="search"><span></span><b><svg width="10" height="10" viewBox="0 0 10 10"><circle cx="4" cy="4" r="3" fill="none" stroke="#fff" stroke-width="1.3"/><line x1="6.2" y1="6.2" x2="9" y2="9" stroke="#fff" stroke-width="1.3"/></svg></b></div>
      <div class="contact">
        <div><strong>CALL US</strong>: +49 30 555 0148</div>
        <div><strong>EMAIL US</strong>: info@betriebsgut-zukunft.de</div>
      </div>
    </div>
    <nav class="nav">
      <ul>
        <li><a class="active" href="#">HOME</a></li>
        <li><a href="#">ABOUT US</a></li>
        <li><a href="#">SERVICES</a></li>
        <li><a href="#">BLOG</a></li>
        <li><a href="#">WORKSHOPS</a></li>
        <li><a href="#">CONTACT US</a></li>
      </ul>
      <div class="social"><i></i><i></i><i></i><i></i><i></i></div>
    </nav>
  </header>

  <section class="hero" role="img" aria-label="Office photo of a consulting team of four business people">
    <div class="hero-text">
      <h1>BETRIEBSGUT ZUKUNFT</h1>
      <p>CONSULTING COMPANY</p>
      <a class="btn btn-ghost" href="#">Click here for more</a>
    </div>
    <span class="arrow prev"><svg width="8" height="8" viewBox="0 0 8 8"><path d="M5.5 1 2.5 4l3 3" fill="none" stroke="#333" stroke-width="1.4"/></svg></span>
    <span class="arrow next"><svg width="8" height="8" viewBox="0 0 8 8"><path d="M2.5 1 5.5 4l-3 3" fill="none" stroke="#333" stroke-width="1.4"/></svg></span>
  </section>

  <section class="welcome">
    <h2 class="section-title">WELCOME TO BETRIEBSGUT ZUKUNFT</h2>
    <p>Lorem Ipsum is simply dummy text of the printing and typesetting industry. Lorem Ipsum has been the industry's standard dummy text ever since the 1500s, when an unknown printer took a galley of type and scrambled it to make a type specimen book. It has survived not only five centuries, but also the leap into electronic typesetting, remaining essentially unchanged.</p>
    <a class="btn" href="#">Read more</a>
  </section>

  <section class="services">
    <div class="kicker">OUR SERVICES TO</div>
    <h2 class="section-title">SMALL AND MEDIUM SIZED COMPANIES</h2>
    <div class="cards">
      <article class="card">
        <div class="photo ph-lead" role="img" aria-label="Chess pieces with a hand moving the king, symbolising leadership"></div>
        <h3>Workshops on Leadership</h3>
        <p>Lorem Ipsum is simply dummy text of the printing and typesetting industry. Lorem Ipsum has been the industry's standard.</p>
        <a class="btn" href="#">Know more</a>
      </article>
      <article class="card">
        <div class="photo ph-health" role="img" aria-label="Colleagues working together at a bright office desk"></div>
        <h3>Employees Health</h3>
        <p>Lorem Ipsum is simply dummy text of the printing and typesetting industry. Lorem Ipsum has been the industry's standard.</p>
        <a class="btn" href="#">Know more</a>
      </article>
      <article class="card">
        <div class="photo ph-edu" role="img" aria-label="Chalkboard sketch about learning and further education"></div>
        <h3>Further Education</h3>
        <p>Lorem Ipsum is simply dummy text of the printing and typesetting industry. Lorem Ipsum has been the industry's standard.</p>
        <a class="btn" href="#">Know more</a>
      </article>
    </div>
  </section>

  <section class="testimonials">
    <h2 class="section-title">TESTIMONIALS</h2>
    <div class="quotes">
      <blockquote class="quote">
        <p>Dummy text is text that is used in the publishing industry or by web designers to occupy the space which will later be filled with 'real' content. This is required when, for example, the final text is not yet available.</p>
        <div class="person"><span class="avatar" role="img" aria-label="Portrait of the client"></span><span>HELENA BRANDT</span></div>
      </blockquote>
      <blockquote class="quote">
        <p>Dummy text is text that is used in the publishing industry or by web designers to occupy the space which will later be filled with 'real' content. This is required when, for example, the final text is not yet available.</p>
        <div class="person"><span class="avatar" role="img" aria-label="Portrait of the client"></span><span>JONAS WELLER</span></div>
      </blockquote>
    </div>
    <div class="pager">‹ ›</div>
  </section>

  <footer class="footer">
    <span>Home | About Us | Services | Blog | Workshops | Contact Us</span>
    <span>© Copyright 2016 All Rights Reserved</span>
  </footer>
</div>
</body>
</html>
```